Landscape design build company door flyer

I would like this flyer to convey a high-level of professionalism for a company that is excellent with communication with their clients as well as a company that does incredible installations

Went on vacation/holiday

```html
<!DOCTYPE html>
<html lang="en">
<head>
<meta charset="utf-8">
<title>Cedarline Builders – Door Flyer</title>
<link href="https://fonts.googleapis.com/css2?family=Montserrat:wght@500;600;700;800&display=swap" rel="stylesheet">
<style>
  :root{
    --navy:#1a3348;
    --orange:#f36f13;
    --white:#ffffff;
    --ink:#1c1c1c;
    --stage:#a2a2a2;
  }
  *{margin:0;padding:0;box-sizing:border-box}
  html,body{width:1200px;height:933px;overflow:hidden;background:var(--stage)}
  body{position:relative;font-family:'Montserrat',sans-serif}
  .flyer{position:absolute;left:257px;top:26px;width:685px;height:881px;background:var(--white);overflow:hidden}
  .abs{position:absolute}

  .hero-photo{left:0;top:215px;width:685px;height:230px;
    background:linear-gradient(100deg,#8e979a 0%,#a89c8c 30%,#b9b3a6 55%,#7c6a55 80%,#5f7a3c 100%)}
  .chevron{left:0;top:0;width:685px;height:260px}
  .brand{left:20px;top:150px;width:190px;display:flex;align-items:center;gap:7px}
  .brand-dot{width:12px;height:12px;border-radius:50%;background:var(--navy);flex:none}
  .brand-name{font-weight:700;font-size:15px;color:var(--orange);letter-spacing:.3px;white-space:nowrap}

  .headline{left:288px;top:42px;line-height:1}
  .headline .line1{display:block;font-weight:800;font-size:46px;color:var(--navy);letter-spacing:1.4px}
  .headline .line2{display:block;font-weight:800;font-size:84px;color:var(--orange);letter-spacing:3px;margin-top:-6px}
  .tagline{left:290px;top:184px;font-weight:700;font-size:25.5px;line-height:27px;color:var(--white);letter-spacing:.2px}

  .thumb-frame{left:29px;top:391px;width:262px;height:112px;background:var(--white)}
  .thumb{left:34px;width:253px;height:103px}
  .thumb.walkway{top:395px;background:linear-gradient(160deg,#6d7a55,#8a9a6e 40%,#aeb4b3 70%,#6f7775)}
  .thumb.porch{top:515px;background:linear-gradient(180deg,#3d4a38 0%,#9c5434 45%,#b8633b 65%,#6f9a3a 100%)}
  .thumb.platform{top:635px;background:linear-gradient(180deg,#8d9096 0%,#8a6a4d 40%,#a3896a 75%,#b09a7f 100%)}

  .section-title{left:313px;font-weight:800;font-size:17px;color:var(--navy);letter-spacing:.2px}
  .rule{left:313px;width:331px;height:1.5px;background:var(--ink)}
  .rule::before{content:"";position:absolute;left:0;top:0;width:81px;height:2.5px;background:var(--orange)}
  .about-title{top:466px}
  .about-rule{top:488px}
  .about-copy{left:313px;top:497px;width:331px;font-weight:500;font-size:12.2px;line-height:14.4px;color:var(--ink);text-align:justify;text-align-last:left}
  .services-title{top:642px}
  .services-rule{top:665px}
  .services{left:313px;top:679px;width:372px;display:grid;grid-template-columns:182px 190px;row-gap:3px;list-style:none}
  .services li{display:flex;align-items:center;gap:7px;font-weight:500;font-size:12.8px;color:var(--ink);height:18px;white-space:nowrap}
  .services svg{width:11px;height:11px;flex:none}

  .cta{left:0;top:767px;width:685px;height:55px;background:var(--navy);display:flex;align-items:center;justify-content:center;
    font-weight:800;font-size:26px;color:var(--white);letter-spacing:.4px}
  .contact{left:0;top:831px;width:685px;height:24px;display:flex;align-items:center;justify-content:center;gap:10px;color:var(--navy);font-weight:700}
  .contact .item{display:flex;align-items:center;gap:6px;white-space:nowrap}
  .contact .phone{font-size:16px}
  .contact .small{font-size:11.5px}
  .contact svg{width:13px;height:13px;flex:none}
  .contact .sep{width:1.5px;height:18px;background:var(--ink)}
</style>
</head>
<body>
<main class="flyer">
  <div class="abs hero-photo" role="img" aria-label="Photo of a finished grey composite deck with cedar railings and stairs"></div>

  <svg class="abs chevron" viewBox="0 0 685 260" aria-hidden="true">
    <polygon points="0,0 155,0 214,172 152,247 0,247 0,215 0,0" fill="#ffffff"/>
    <rect x="0" y="0" width="685" height="172" fill="#ffffff"/>
    <polygon points="214,172 685,172 685,247 152,247" fill="#f36f13"/>
    <polyline points="149,0 262,125 214,176" fill="none" stroke="#111" stroke-width="12" stroke-linejoin="miter"/>
  </svg>

  <div class="abs brand">
    <span class="brand-dot"></span>
    <span class="brand-name">CEDARLINE BUILDERS</span>
  </div>

  <h1 class="abs headline">
    <span class="line1">LOVE COMING</span>
    <span class="line2">HOME?</span>
  </h1>
  <p class="abs tagline">LET US REIMAGINE YOUR<br>OUTDOOR LIVING AREA</p>

  <div class="abs thumb-frame"></div>
  <div class="abs thumb walkway" role="img" aria-label="Photo of a paver walkway with stone steps and planted retaining walls"></div>
  <div class="abs thumb porch" role="img" aria-label="Photo of a cabin with a wraparound stained wood porch and railings"></div>
  <div class="abs thumb platform" role="img" aria-label="Photo of a low wooden deck platform with wide steps"></div>

  <h2 class="abs section-title about-title">ABOUT US</h2>
  <div class="abs rule about-rule"></div>
  <p class="abs about-copy">Discover the endless possibilities for your outdoor space with The Cedarline Builders Team. Our team of skilled artisans is dedicated to turning your outdoor space into a breathtaking oasis that you’ll love coming home to. Whether it’s a cozy patio for intimate gatherings, a sprawling deck to host memorable parties, or a custom paver driveway that adds instant curb appeal, our high-quality craftsmanship ensures stunning results that exceed your expectations.</p>

  <h2 class="abs section-title services-title">OUR SERVICES</h2>
  <div class="abs rule services-rule"></div>
  <ul class="abs services">
    <li><svg viewBox="0 0 12 12"><circle cx="6" cy="6" r="6" fill="#f36f13"/><path d="M3.2 6.2l2 2 3.8-4" stroke="#fff" stroke-width="1.6" fill="none"/></svg>PAVER PATIOS</li>
    <li><svg viewBox="0 0 12 12"><circle cx="6" cy="6" r="6" fill="#f36f13"/><path d="M3.2 6.2l2 2 3.8-4" stroke="#fff" stroke-width="1.6" fill="none"/></svg>POOLS</li>
    <li><svg viewBox="0 0 12 12"><circle cx="6" cy="6" r="6" fill="#f36f13"/><path d="M3.2 6.2l2 2 3.8-4" stroke="#fff" stroke-width="1.6" fill="none"/></svg>PAVER DRIVEWAYS</li>
    <li><svg viewBox="0 0 12 12"><circle cx="6" cy="6" r="6" fill="#f36f13"/><path d="M3.2 6.2l2 2 3.8-4" stroke="#fff" stroke-width="1.6" fill="none"/></svg>OUTDOOR LIGHTING</li>
    <li><svg viewBox="0 0 12 12"><circle cx="6" cy="6" r="6" fill="#f36f13"/><path d="M3.2 6.2l2 2 3.8-4" stroke="#fff" stroke-width="1.6" fill="none"/></svg>RETAINING WALLS</li>
    <li><svg viewBox="0 0 12 12"><circle cx="6" cy="6" r="6" fill="#f36f13"/><path d="M3.2 6.2l2 2 3.8-4" stroke="#fff" stroke-width="1.6" fill="none"/></svg>FIREPITS &amp; FIREPLACES</li>
    <li><svg viewBox="0 0 12 12"><circle cx="6" cy="6" r="6" fill="#f36f13"/><path d="M3.2 6.2l2 2 3.8-4" stroke="#fff" stroke-width="1.6" fill="none"/></svg>DECKS &amp; RAILINGS</li>
    <li><svg viewBox="0 0 12 12"><circle cx="6" cy="6" r="6" fill="#f36f13"/><path d="M3.2 6.2l2 2 3.8-4" stroke="#fff" stroke-width="1.6" fill="none"/></svg>AND MORE...</li>
  </ul>

  <div class="abs cta">CONTACT US TODAY FOR A FREE ESTIMATE</div>

  <div class="abs contact">
    <span class="item phone"><svg viewBox="0 0 24 24"><path d="M6.6 10.8a15.5 15.5 0 006.6 6.6l2.2-2.2c.3-.3.7-.4 1-.2 1.1.4 2.3.6 3.6.6.6 0 1 .4 1 1V20c0 .6-.4 1-1 1C10.6 21 3 13.4 3 4c0-.6.4-1 1-1h3.5c.6 0 1 .4 1 1 0 1.3.2 2.5.6 3.6.1.3 0 .7-.2 1z" fill="#f36f13"/></svg>206-555-0148</span>
    <span class="sep"></span>
    <span class="item small"><svg viewBox="0 0 24 24"><rect x="2" y="5" width="20" height="14" rx="1" fill="#f36f13"/><path d="M3 6l9 7 9-7" stroke="#fff" stroke-width="1.8" fill="none"/></svg>INFO@CEDARLINEBUILDERS.COM</span>
    <span class="sep"></span>
    <span class="item small"><svg viewBox="0 0 24 24"><g fill="none" stroke="#f36f13" stroke-width="1.8"><circle cx="12" cy="12" r="9.5"/><ellipse cx="12" cy="12" rx="4.2" ry="9.5"/><path d="M2.5 12h19M4 7h16M4 17h16"/></g></svg>WWW.CEDARLINEBUILDERS.COM</span>
  </div>
</main>
</body>
</html>
```